Dynamic Business Card for Sports Supplements Company

Hi! I'm looking for an awesome business card to match my existing sports supplement company. I have uploaded my current company logo and screenshot of the front page of my website.

I would like to have something dynamic and interesting and utilize the colors in the website - the reds and purples

The business card should be double sided and focus on a unique eye-catching design on the back and include all the relevant company info.

Most importantly, it should say somewhere: "Sign up on our website for a coupon code."

Target Market(s)

Mostly for women gym goers but it shouldn't be too feminine. It should be in keeping with the website design. It should flow and clearly be connected to it

Industry/Entity Type

Business

Contact Information for Business Card

Lorraine K. Vestal
CEO
LVestal@Quorvanexco.com
www.quorvanexco.com
555.417.3820
P.O. Box 47315
Dunmere, Calvania 00000

Sign up on our website for a coupon code

Font styles to use
Serif
Sans Serif
Other font styles liked:
• Novecento font family and "Quorvanex" is in AR Destine font

Requirements
Must have
• One side should be a bold Quorvanex logo design. Even just the symbol itself may be o.k. (see attached file)

```html
<!DOCTYPE html>
<html lang="en">
<head>
<meta charset="utf-8">
<title>Quorvanex Business Card</title>
<link rel="stylesheet" href="https://fonts.googleapis.com/css2?family=Source+Sans+3:wght@400;600&display=swap">
<style>
  :root {
    --stage: #000000;
    --slate-light: #4a525d;
    --slate-mid: #353b45;
    --slate-dark: #22262d;
    --ink: #ffffff;
    --accent: #e3262b;
    --rule: #9aa0a8;
  }
  * { margin: 0; padding: 0; box-sizing: border-box; }
  html, body {
    width: 1200px; height: 900px; overflow: hidden;
    background: var(--stage);
    font-family: "Source Sans 3", Arial, sans-serif;
    color: var(--ink);
  }
  .stage { position: relative; width: 1200px; height: 900px; }
  .card {
    position: absolute; top: 271px;
    width: 457px; height: 281px;
    border-radius: 14px; overflow: hidden;
    background:
      radial-gradient(ellipse at 50% 35%, var(--slate-light) 0%, var(--slate-mid) 55%, var(--slate-dark) 100%);
  }
  .card-front { left: 137px; }
  .card-back { left: 626px; }

  .brand { position: absolute; display: flex; align-items: center; gap: 8px; }
  .brand-mark { width: 14px; height: 14px; background: var(--accent); }
  .brand-name { font-weight: 600; font-size: 27px; letter-spacing: 1px; color: var(--ink); line-height: 1; }
  .card-front .brand { left: 30px; top: 100px; }
  .card-back .brand { left: 0; right: 0; top: 165px; justify-content: center; }
  .card-back .brand-name { font-size: 29px; }

  .holder-name {
    position: absolute; right: 23px; top: 149px;
    color: var(--accent); font-size: 17px; letter-spacing: .3px;
  }
  .holder-rule {
    position: absolute; left: 30px; top: 180px; width: 360px; height: 1px;
    background: var(--rule);
  }
  .holder-title { position: absolute; right: 25px; top: 171px; font-size: 13px; }

  .contact-list { position: absolute; left: 28px; top: 197px; list-style: none; }
  .contact-list li { display: flex; align-items: center; gap: 6px; font-size: 13.5px; height: 20.5px; }
  .contact-list svg { width: 12px; height: 12px; fill: var(--accent); }

  .postal {
    position: absolute; right: 22px; top: 220px;
    text-align: right; font-size: 13.5px; line-height: 19px; font-style: normal;
  }

  .signup {
    position: absolute; left: 0; right: 0; top: 229px;
    text-align: center; font-size: 13.5px; letter-spacing: .2px;
  }
  .signup .highlight { color: var(--accent); }
</style>
</head>
<body>
<main class="stage">
  <section class="card card-front">
    <div class="brand">
      <span class="brand-mark"></span>
      <span class="brand-name">QUORVANEX</span>
    </div>
    <p class="holder-name">LORRAINE K. VESTAL</p>
    <div class="holder-rule"></div>
    <p class="holder-title">CEO</p>
    <ul class="contact-list">
      <li>
        <svg viewBox="0 0 12 12"><path d="M1 4c0-2 2-3 5-3s5 1 5 3v1H8.5V3.8h-5V5H1z"/><path d="M2.5 6h7l1 5h-9z"/></svg>
        555.417.3820
      </li>
      <li>
        <svg viewBox="0 0 12 12"><path d="M1 2.5h10v1L6 7 1 3.5z"/><path d="M1 5l5 3.5L11 5v4.5H1z"/></svg>
        LVestal@Quorvanexco.com
      </li>
      <li>
        <svg viewBox="0 0 12 12"><circle cx="6" cy="6" r="5.3"/></svg>
        www.quorvanexco.com
      </li>
    </ul>
    <address class="postal">
      P.O. Box 47315<br>
      Dunmere, Calvania 00000
    </address>
  </section>

  <section class="card card-back">
    <div class="brand">
      <span class="brand-mark"></span>
      <span class="brand-name">QUORVANEX</span>
    </div>
    <p class="signup">SIGN UP ON OUR <span class="highlight">WEBSITE</span> FOR A COUPON CODE</p>
  </section>
</main>
</body>
</html>
```